Lucky Harbour Fun Casino Entertainment

Looking to update my business card and make it look more modern, stand out and eye catching.
We are are fun casino business in Australia (primarily Sydney). Blackjack and Roulette are our most popular games although we have pretty much every game available for hire that you would find in a real casino. The final design would need to be sleek and appeal to the more upmarket corporate sector.
We mainly cater for Corporate Events, Private Parties, Fundraising Events, Team Building, Poker Tournaments
I think I'd prefer the colour Black.

Target Market(s)

High-end Corporate

Industry/Entity Type

Events

Contact Information for Business Card

Rob Kendall
Director
1300 482 617
0433 728 591
info@luckyharbour.com.au
www.luckyharbour.com.au
Facebook & Instagram @luckyharbourevents (proper social icons preferred)

Colors
000000
0255a3

Requirements
Must have
• Front side:
• Logo
• Contact details
• 'Australia's #1 Fun Casino Specialists'
• Back:
• Logo
Nice to have
• Back:
• Corporate Events
• Private Parties
• Poker Tournaments
• Fundraising
• Props & Theming
• Photo Booth
• Horse Racing Events
• The Vegas Sign attached, maybe on the back of the card in the background...?

```html
<!DOCTYPE html>
<html lang="en">
<head>
<meta charset="utf-8">
<title>Lucky Harbour – Business Card Front</title>
<link rel="stylesheet" href="https://fonts.googleapis.com/css2?family=Lato:wght@400;700&family=Roboto:wght@400&display=swap">
<style>
  :root {
    --page-bg: #e6e6e6;
    --card-black: #000000;
    --accent-gold: #f7a81b;
    --text-light: #ffffff;
    --text-muted: #d6d6d6;
    --rule: #8a8a8a;
    --social-blue: #0255a3;
    --disc-light: #ffffff;
    --disc-shade: #cfcfcf;
    --logo-ink: #111111;
  }
  * { box-sizing: border-box; margin: 0; padding: 0; }
  html, body {
    width: 1200px; height: 900px; overflow: hidden;
    background: var(--page-bg);
  }
  .card {
    position: absolute; left: 111px; top: 148px;
    width: 978px; height: 604px;
    background: var(--card-black);
    font-family: "Lato", sans-serif;
    color: var(--text-light);
    box-shadow: 0 10px 30px rgba(0,0,0,.25);
  }
  .holder-name {
    position: absolute; left: 44px; top: 64px;
    font-weight: 700; font-size: 38px; letter-spacing: .5px;
    color: var(--accent-gold); line-height: 1;
  }
  .holder-role {
    position: absolute; left: 44px; top: 110px;
    font-size: 24px; color: var(--text-muted); line-height: 1;
  }
  .contact-list { position: absolute; left: 44px; top: 160px; list-style: none; }
  .contact-item {
    display: flex; align-items: center; gap: 8px;
    height: 36px; font-size: 25px; line-height: 1;
    color: var(--text-light);
  }
  .contact-icon { width: 22px; height: 22px; flex: none; fill: var(--accent-gold); }
  .social-list { position: absolute; left: 44px; top: 322px; list-style: none; }
  .social-item {
    display: flex; align-items: center; gap: 8px;
    height: 45px; font-size: 25px; line-height: 1;
  }
  .social-dot {
    width: 33px; height: 33px; border-radius: 50%;
    background: var(--social-blue); flex: none;
  }
  .divider {
    position: absolute; left: 45px; top: 446px;
    width: 398px; height: 2px; background: var(--rule);
  }
  .tagline {
    position: absolute; left: 48px; top: 470px;
    font-family: "Roboto", sans-serif; font-size: 27px;
    line-height: 36px; color: var(--accent-gold);
    text-transform: uppercase;
  }
  .logo-disc {
    position: absolute; left: 431px; top: 38px;
    width: 524px; height: 524px; border-radius: 50%;
    background: radial-gradient(circle at 50% 45%, var(--disc-light) 0%, #f1f1f1 55%, var(--disc-shade) 100%);
    display: flex; align-items: center; justify-content: center;
  }
  .logo-name {
    font-family: "Lato", sans-serif; font-weight: 700;
    font-size: 52px; letter-spacing: 1px;
    color: var(--logo-ink); text-transform: uppercase;
  }
</style>
</head>
<body>
  <article class="card">
    <h1 class="holder-name">ROB KENDALL</h1>
    <p class="holder-role">Director</p>

    <ul class="contact-list">
      <li class="contact-item">
        <svg class="contact-icon" viewBox="0 0 24 24" aria-hidden="true"><path d="M3 9c0-3 4-5 9-5s9 2 9 5v1h-5V8.5C14.5 8 9.5 8 8 8.5V10H3z M6 12h12l2 8H4z M12 13.5a2.5 2.5 0 1 0 0.01 0z"/></svg>
        <span>1300 482 617</span>
      </li>
      <li class="contact-item">
        <svg class="contact-icon" viewBox="0 0 24 24" aria-hidden="true"><path d="M7 2h10a1.5 1.5 0 0 1 1.5 1.5v17A1.5 1.5 0 0 1 17 22H7a1.5 1.5 0 0 1-1.5-1.5v-17A1.5 1.5 0 0 1 7 2zm.5 3v13h9V5zm4.5 14.2a1 1 0 1 0 .01 0z"/></svg>
        <span>0433 728 591</span>
      </li>
      <li class="contact-item">
        <svg class="contact-icon" viewBox="0 0 24 24" aria-hidden="true"><path d="M2 5h20v14H2zm2 2v.5l8 5.5 8-5.5V7zm0 3v7h16v-7l-8 5.5z"/></svg>
        <span>info@luckyharbour.com.au</span>
      </li>
      <li class="contact-item">
        <svg class="contact-icon" viewBox="0 0 24 24" aria-hidden="true"><path d="M12 2a10 10 0 1 0 0.01 0zm-1 3.2c-1 .6-2.5 1.4-2.5 2.8 0 1.5 2 1.2 2.5 2.5.4 1.1-1.6 1.700-1.3 3.3.3 1.3 2 1.6 2 3.5v2.3A8 8 0 0 1 4.3 9.5c1.3.2 2.4-.6 2.7-1.8A8 8 0 0 1 11 5.2zm3.5.6a8 8 0 0 1 4.8 10.6c-.6-.9-1.8-1-2.4-2.2-.6-1.3.4-2.6-.8-3.5-1-.8-2.5 0-3.1-1.2-.5-1.1 1.5-2 1.5-3.7z"/></svg>
        <span>www.luckyharbour.com.au</span>
      </li>
    </ul>

    <ul class="social-list">
      <li class="social-item"><span class="social-dot" aria-hidden="true"></span><span>@luckyharbourevents</span></li>
      <li class="social-item"><span class="social-dot" aria-hidden="true"></span><span>@luckyharbourevents</span></li>
    </ul>

    <div class="divider"></div>
    <p class="tagline">Australia’s #1 Fun Casino<br>Specialists</p>

    <div class="logo-disc">
      <span class="logo-name">Lucky Harbour</span>
    </div>
  </article>
</body>
</html>
```